Business Card Design

New business card design

Target Market(s)

Residential & Commercial Property Managers

Industry/Entity Type

Plumbing Services

Contact Information for Business Card

Name - Rowan Keddle, title - Director, Phone Number - 0431 286 517, email - rowan@tbk-plumbing.com.au, Company ABN - 73 215 904 386,

Font styles to use
Sans Serif

Colors
0054AA
0677BA
7BADD7
CADEEF
E8F1F8

```html
<!DOCTYPE html>
<html lang="en">
<head>
<meta charset="utf-8">
<title>TBK Plumbing Services – Business Cards</title>
<link rel="stylesheet" href="https://fonts.googleapis.com/css2?family=Open+Sans:ital,wght@0,300;0,400;0,600;1,400&display=swap">
<style>
  :root {
    --bg: #e9e6e1;
    --card: #cbeaf9;
    --band: #2aa6e0;
    --wash: #9edcf4;
    --wash-light: #bfe7f8;
    --ink: #1e2a33;
    --muted: #6f6a60;
    --white: #ffffff;
  }
  * { box-sizing: border-box; margin: 0; padding: 0; }
  html, body {
    width: 1200px; height: 900px; overflow: hidden;
    background: var(--bg);
    font-family: "Open Sans", Arial, sans-serif;
  }
  .canvas {
    width: 1200px; height: 900px;
    display: flex; flex-direction: column;
    align-items: center; justify-content: center; gap: 40px;
  }
  .card {
    position: relative;
    width: 700px; height: 400px;
    background: var(--card);
    overflow: hidden;
    box-shadow: 0 10px 24px rgba(0,0,0,0.18);
  }
  .wordmark { position: absolute; color: var(--ink); font-weight: 400; }
  .wordmark__name { display: block; font-size: 130px; line-height: 1; letter-spacing: 2px; }
  .wordmark__tag { display: block; font-size: 16px; letter-spacing: 13px; margin-top: 6px; }

  /* front */
  .card--front .wordmark { left: 110px; top: 70px; }
  .front-band { position: absolute; left: 0; bottom: 0; width: 700px; height: 90px; }
  .abn {
    position: absolute; left: 270px; bottom: 28px; width: 310px;
    text-align: center; color: var(--white);
    font-size: 19px; font-weight: 300; letter-spacing: 0.5px;
  }

  /* back */
  .wash {
    position: absolute; left: 0; top: 0; width: 220px; height: 400px;
    background: linear-gradient(90deg, var(--wash) 70%, var(--wash-light));
  }
  .card--back .wordmark { left: 260px; top: 40px; }
  .card--back .wordmark__name { font-size: 100px; }
  .card--back .wordmark__tag { font-size: 13px; letter-spacing: 10px; }
  .contact {
    position: absolute; left: 380px; top: 225px;
    color: var(--ink); text-align: center;
  }
  .contact__name { font-size: 30px; font-weight: 600; letter-spacing: -0.5px; }
  .contact__role { font-size: 19px; font-style: italic; margin-bottom: 10px; }
  .contact__line {
    display: flex; align-items: center; gap: 8px; justify-content: flex-start;
    font-size: 18px; line-height: 1.6;
  }
  .contact__line svg { width: 15px; height: 15px; fill: var(--muted); }
</style>
</head>
<body>
<main class="canvas">

  <section class="card card--front" aria-label="Business card front">
    <div class="wordmark">
      <span class="wordmark__name">tbk</span>
      <span class="wordmark__tag">plumbing services</span>
    </div>
    <svg class="front-band" viewBox="0 0 700 90" preserveAspectRatio="none" aria-hidden="true">
      <path fill="var(--band)" d="M0 72 H240 C262 72 262 20 286 20 H570 C594 20 594 72 616 72 H700 V90 H0 Z"/>
    </svg>
    <p class="abn">ABN - 73 215 904 386</p>
  </section>

  <section class="card card--back" aria-label="Business card back">
    <div class="wash" role="img" aria-label="Soft blue water decoration"></div>
    <div class="wordmark">
      <span class="wordmark__name">tbk</span>
      <span class="wordmark__tag">plumbing services</span>
    </div>
    <div class="contact">
      <p class="contact__name">Rowan Keddle</p>
      <p class="contact__role">Director</p>
      <p class="contact__line">
        <svg viewBox="0 0 24 24" aria-hidden="true"><path d="M6.6 10.8a15 15 0 0 0 6.6 6.6l2.2-2.2c.3-.3.7-.4 1-.2 1.1.4 2.3.6 3.6.6.6 0 1 .4 1 1V20c0 .6-.4 1-1 1A17 17 0 0 1 3 4c0-.6.4-1 1-1h3.5c.6 0 1 .4 1 1 0 1.3.2 2.5.6 3.6.1.3 0 .7-.2 1z"/></svg>
        0431 286 517
      </p>
      <p class="contact__line">
        <svg viewBox="0 0 24 24" aria-hidden="true"><path d="M2 5h20v14H2z M2 5l10 8 10-8" fill="none" stroke="var(--muted)" stroke-width="2.4"/></svg>
        rowan@tbk-plumbing.com.au
      </p>
    </div>
  </section>

</main>
</body>
</html>
```